Simple, 1-Page Project - Life-saving AED Devices

We recently kicked off a project to bring all geographic location records for automatic emergency defibrillators (AEDs) in the State of New York online (instead of kept in paper in drawers). This hope is that is will ultimately save thousands of lives, as 9-1-1 operators will be able to quickly direct civilians to the nearest AED to bring to people suffering a cardiac event (e.g., a heart attack).

This page will be used to describe this effort, our progress thus far and how far we have left to go.

I am looking for a 1-page design - coded for both a responsive version for mobile devices and a traditional version - that would ***ideally*** plug into my existing WordPress site (https://qv-lmt.org), but it's not a requirement.

Target Market(s)

General public (non-physicians/non-EMTs)

Requirements
Must have
• - Our logo (please note, our logo is the Birchfield Vale Chapter logo...attached)
Nice to have
• - Would be wonderful to have an area with a clickable map showing where the participating regions are - which, once clicked, will take to you their specific sites. Regions are large chunks of land encompassing multiple towns, NOT a singular, specific place A nice-looking Plumtail Grids Map, a la Plumtail Grids (https://plumtailgrids.com/) would be cool if this were possible..
• - If you need a headline or page title, you can use: "Bringing AEDs in New York Online"
• - Would be nice if the design incorporated the color scheme of our brand (see attachment) and/or our main website: https://qv-lmt.org/
• - Would be nice to have some AED imagery - I attached some common symbols seen in AED advertising for inspiration
Should not have
• - This is a serious topic, so the design should be respectful and not too silly/cartoonish
• - Stock images, if chosen, should be thoughtful and classy

```html
<!DOCTYPE html>
<html lang="en">
<head>
<meta charset="utf-8">
<title>Bringing AEDs in New York Online – Birchfield Vale Chapter</title>
<link rel="stylesheet" href="https://fonts.googleapis.com/css2?family=Poppins:wght@400;500;600;700&family=Lato:wght@400;700&family=Roboto:wght@400;500;700&display=swap">
<style>
:root{
  --navy:#1d3566;
  --navy-deep:#142a55;
  --blue:#2c4ea0;
  --orange:#f7941d;
  --orange-dark:#ef7f10;
  --red:#e5322d;
  --white:#ffffff;
  --grey-bg:#f2f2f2;
  --text:#666a70;
  --dark:#222;
}
*{box-sizing:border-box;margin:0;padding:0}
html,body{width:1200px;height:4041px;overflow:hidden}
body{position:relative;font-family:'Poppins',sans-serif;color:var(--dark);background:var(--white)}
.abs{position:absolute}
a{color:inherit;text-decoration:none}

/* top bar */
.topbar{left:0;top:0;width:1200px;height:57px;background:var(--white)}
.topbar .contact{left:89px;top:20px;font-family:'Roboto',sans-serif;font-size:15px;color:#333;display:flex;align-items:center;gap:8px}
.topbar .social{right:86px;top:20px;display:flex;gap:14px}
.social-dot{width:16px;height:16px;border-radius:3px;background:#333}

/* nav */
.nav{left:0;top:57px;width:1200px;height:68px;background:linear-gradient(90deg,#1b3468,#243f78)}
.nav a{position:absolute;top:24px;color:var(--white);font-size:15px;font-weight:500}
.brand-disc{left:518px;top:0;width:172px;height:168px;border-radius:50%;background:var(--white);display:flex;flex-direction:column;align-items:center;justify-content:center;text-align:center;z-index:3}
.brand-disc .ring{width:64px;height:64px;border-radius:50%;border:3px solid var(--navy);margin-bottom:6px}
.brand-disc span{font-family:'Roboto',sans-serif;font-size:14px;font-weight:500;color:var(--navy);line-height:1.2;width:120px}

/* hero */
.hero{left:0;top:125px;width:1200px;height:553px;background:linear-gradient(160deg,#5c5850 0%,#3d3a36 45%,#6e665a 75%,#2f2d2b 100%)}
.hero::after{content:"";position:absolute;inset:0;background:rgba(10,15,30,.35)}
.hero-content{position:absolute;left:0;top:150px;width:1200px;text-align:center;color:var(--white);z-index:2}
.hero h1{font-size:54px;font-weight:700;line-height:1.1}
.hero p{margin:26px auto 0;width:820px;font-family:'Roboto',sans-serif;font-size:17px;line-height:32px}
.btn-outline{display:inline-block;margin-top:24px;width:218px;height:60px;line-height:56px;border:2px solid var(--white);border-radius:30px;font-size:23px;font-weight:600;letter-spacing:.3px}
.hero-arrow{top:345px;width:42px;height:42px;border-radius:50%;background:rgba(30,55,110,.85);z-index:2;display:flex;align-items:center;justify-content:center}
.hero-base{left:0;top:620px;width:1200px;height:130px;z-index:2}
.hero-emblem{left:556px;top:656px;width:94px;height:94px;border-radius:50%;border:3px solid var(--navy);z-index:3;display:flex;align-items:center;justify-content:center;text-align:center;font-family:'Roboto',sans-serif;font-size:10px;font-weight:500;color:var(--navy);line-height:1.2;padding:8px}

/* about */
.about h2{left:88px;top:840px;font-size:46px;font-weight:700;color:var(--blue)}
.about p{left:88px;top:904px;width:527px;font-family:'Lato',sans-serif;font-size:17.5px;line-height:31.4px;color:var(--text);text-align:justify}
.btn-orange{background:var(--orange);color:var(--white);border-radius:26px;text-align:center;font-weight:600}
.about .btn-orange{left:88px;top:1178px;width:168px;height:50px;line-height:50px;font-size:21px}
.about-media{left:640px;top:845px;width:480px;height:420px}

/* services */
.services{left:0;top:1341px;width:1200px;height:742px;background:linear-gradient(135deg,#1b3263,#243d72 50%,#1b3263)}
.services h2{position:absolute;left:0;top:76px;width:1200px;text-align:center;color:var(--white);font-size:46px;font-weight:600}
.service{position:absolute;top:160px;width:290px;text-align:center;color:var(--white)}
.service svg{display:block;margin:0 auto;overflow:visible}
.service h3{margin-top:44px;font-size:20px;font-weight:500}
.service p{margin-top:14px;font-size:16px;font-weight:600;line-height:23.5px}
.divider{position:absolute;top:419px;width:2px;height:92px;background:rgba(255,255,255,.75)}
.services .btn-orange{position:absolute;left:477px;top:596px;width:246px;height:60px;line-height:60px;font-size:20px;border-radius:30px}

/* news */
.news{left:0;top:2083px;width:1200px;height:717px;background:var(--grey-bg)}
.news h2{position:absolute;left:0;top:76px;width:1200px;text-align:center;font-size:46px;font-weight:600;color:var(--navy)}
.date{position:absolute;left:0;top:0;width:57px;height:58px;background:var(--orange);color:var(--white);font-family:'Roboto',sans-serif;font-size:17px;line-height:22px;padding:7px 0 0 9px;z-index:2}
.card-main{left:89px;top:157px;width:496px;height:471px;background:linear-gradient(160deg,#d6d8da 0%,#8a8c8e 40%,#7a2a2e 70%,#3c2426 100%);box-shadow:0 3px 8px rgba(0,0,0,.25)}
.card-main .overlay{position:absolute;left:0;bottom:0;width:100%;height:160px;background:linear-gradient(transparent,rgba(0,0,0,.7))}
.card-main h4{position:absolute;left:18px;top:366px;width:400px;color:var(--white);font-size:18px;font-weight:600;line-height:28px}
.card-main .meta{position:absolute;left:18px;top:430px;color:var(--white);font-size:15px;display:flex;align-items:center}
.card-side{left:610px;width:497px;height:224px;background:var(--white);box-shadow:0 3px 8px rgba(0,0,0,.15)}
.card-side .thumb{position:absolute;left:0;top:0;width:242px;height:224px}
.card-side .body{position:absolute;left:259px;top:6px;width:230px}
.card-side h4{font-size:18px;font-weight:600;line-height:26px;color:#222}
.card-side p{margin-top:6px;font-family:'Roboto',sans-serif;font-size:13.5px;line-height:20.5px;color:#888;text-align:justify}
.card-side .meta{position:absolute;left:242px;bottom:0;width:255px;height:42px;background:#f4f4f4;display:flex;align-items:center;font-family:'Roboto',sans-serif;font-size:14px;color:#666}
.meta .views{margin-left:8px}
.meta .more{font-weight:600;display:flex;align-items:center;gap:6px}
.card-side .more{color:var(--red);position:absolute;right:10px;font-size:16px}

/* map + form */
.map{left:0;top:2800px;width:1200px;height:463px;background:linear-gradient(120deg,#e9eaec,#f5f5f6 40%,#e6e7e9)}
.form-card{left:191px;top:3051px;width:818px;height:444px;background:var(--white);box-shadow:0 2px 14px rgba(0,0,0,.15)}
.form-card h3{position:absolute;left:70px;top:48px;font-size:25px;font-weight:500;color:#333}
.field{position:absolute;border:1px solid #ccc;font-family:'Roboto',sans-serif;font-size:13px;color:#777;padding:15px 20px}
.form-card .btn-submit{position:absolute;left:334px;top:347px;width:161px;height:42px;line-height:42px;background:var(--orange);color:var(--white);text-align:center;font-size:19px;font-weight:600}

/* contact strip */
.info{top:3600px;display:flex;gap:18px}
.info .icon{width:56px;height:56px;border:2px dashed var(--orange);display:flex;align-items:center;justify-content:center}
.info h5{font-size:18px;font-weight:600;color:#333;margin-top:3px}
.info p{font-family:'Roboto',sans-serif;font-size:15px;color:#555;line-height:21px;margin-top:2px}

/* footer */
.footer{left:0;top:3741px;width:1200px;height:300px;background:linear-gradient(90deg,#1b3468,#243f78)}
.footer .ring{position:absolute;left:397px;top:20px;width:112px;height:112px;border-radius:50%;border:3px solid var(--white)}
.footer .sep{position:absolute;left:528px;top:38px;width:2px;height:80px;background:var(--white)}
.footer .name{position:absolute;left:548px;top:40px;color:var(--white);font-family:'Roboto',sans-serif;font-size:40px;font-weight:400;line-height:44px}
.footer .name small{display:block;font-size:18px;line-height:26px;letter-spacing:1px}
.footer nav{position:absolute;left:0;top:150px;width:1200px;text-align:center}
.footer nav a{color:var(--white);font-size:16px;font-weight:500;margin:0 13px}
.footer .social{position:absolute;left:520px;top:196px;display:flex;gap:16px}
.footer .social span{width:28px;height:28px;background:var(--white)}
.footer .copy{position:absolute;left:0;top:243px;width:1200px;text-align:center;color:var(--white);font-size:19px}
</style>
</head>
<body>

<header>
  <div class="abs topbar">
    <div class="abs contact">
      <svg width="14" height="14" viewBox="0 0 24 24"><path fill="#333" d="M6.6 10.8a15 15 0 006.6 6.6l2.2-2.2c.3-.3.7-.4 1-.2 1.1.4 2.3.6 3.6.6.6 0 1 .4 1 1V20c0 .6-.4 1-1 1A17 17 0 013 4c0-.6.4-1 1-1h3.5c.6 0 1 .4 1 1 0 1.3.2 2.5.6 3.6.1.3 0 .7-.2 1z"/></svg>
      800 555 0142 |
      <svg width="15" height="12" viewBox="0 0 24 18"><rect width="24" height="18" rx="2" fill="#333"/><path d="M2 2l10 8 10-8" stroke="#fff" stroke-width="2" fill="none"/></svg>
      hello@aedlocator.org
    </div>
    <div class="abs social" aria-label="Social links">
      <span class="social-dot"></span><span class="social-dot"></span><span class="social-dot"></span><span class="social-dot"></span>
    </div>
  </div>

  <nav class="abs nav">
    <a style="left:89px">Home</a>
    <a style="left:209px">About Us</a>
    <a style="left:351px">Services &amp; Products</a>
    <a style="left:712px">Resources</a>
    <a style="left:865px">Blog</a>
    <a style="left:974px">Contact Us</a>
  </nav>
  <div class="abs brand-disc">
    <div class="ring"></div>
    <span>Birchfield Vale Chapter</span>
  </div>
</header>

<section class="abs hero" role="img" aria-label="Photo of rescuers performing CPR with an AED on a patient lying on sand">
  <div class="hero-content">
    <h1>Bringing AEDs in New York Online</h1>
    <p>Lorem Ipsum is simply dummy text of the printing and typesetting industry. Lorem Ipsum has been the industry's standard dummy text ever since</p>
    <a class="btn-outline">GET STARTED</a>
  </div>
  <div class="abs hero-arrow" style="left:28px"><svg width="12" height="12" viewBox="0 0 12 12"><path d="M8 1L3 6l5 5" stroke="#fff" stroke-width="2" fill="none"/></svg></div>
  <div class="abs hero-arrow" style="left:1138px"><svg width="12" height="12" viewBox="0 0 12 12"><path d="M4 1l5 5-5 5" stroke="#fff" stroke-width="2" fill="none"/></svg></div>
</section>
<svg class="abs hero-base" viewBox="0 0 1200 130" preserveAspectRatio="none">
  <path d="M0 58 L470 58 C530 58 540 12 600 12 C660 12 670 58 730 58 L1200 58 L1200 130 L0 130 Z" fill="#fff"/>
</svg>
<div class="abs hero-emblem">Birchfield Vale Chapter</div>

<section class="about">
  <h2 class="abs">ABOUT US</h2>
  <p class="abs">Lorem Ipsum is simply dummy text of the printing and typesetting industry. Lorem Ipsum has been the industry's standard dummy text ever since the 1500s, when an unknown printer took a galley of type and scrambled it to make a type specimen book. It has survived not only five centuries, but also the leap into electronic typesetting, remaining essentially unchanged. It was popularised in the 1960s with the release of Letraset sheets containing Lorem Ipsum passages and more recently</p>
  <a class="abs btn-orange">Read More</a>
  <svg class="abs about-media" viewBox="0 0 480 420" role="img" aria-label="Circular photos of an AED kit, an AED wall sign and training pads on a manikin">
    <defs>
      <linearGradient id="gA" x1="0" y1="0" x2="1" y2="1"><stop offset="0" stop-color="#7d8a5a"/><stop offset=".5" stop-color="#3a3e58"/><stop offset="1" stop-color="#b08a72"/></linearGradient>
      <linearGradient id="gB" x1="0" y1="0" x2="0" y2="1"><stop offset="0" stop-color="#ddd"/><stop offset="1" stop-color="#c43030"/></linearGradient>
      <linearGradient id="gC" x1="0" y1="0" x2="1" y2="1"><stop offset="0" stop-color="#e8e6e2"/><stop offset="1" stop-color="#8aa6c4"/></linearGradient>
    </defs>
    <circle cx="380" cy="160" r="88" fill="url(#gB)" stroke="#f7941d" stroke-width="7"/>
    <circle cx="356" cy="308" r="96" fill="url(#gC)" stroke="#f7941d" stroke-width="7"/>
    <circle cx="176" cy="182" r="168" fill="url(#gA)" stroke="#f7941d" stroke-width="10"/>
  </svg>
</section>

<section class="abs services" role="region" aria-label="Our services">
  <h2>OUR SERVICES</h2>

  <div class="service" style="left:111px">
    <svg width="240" height="200" viewBox="0 0 240 200">
      <path d="M30 78 A100 100 0 0 1 214 72" stroke="#f7941d" stroke-width="3" fill="none"/>
      <path d="M204 80 L228 70 L222 94 Z" fill="none" stroke="#f7941d" stroke-width="3" stroke-linejoin="round"/>
      <circle cx="120" cy="110" r="76" fill="#f7941d"/>
      <circle cx="26" cy="71" r="17" fill="#f7941d"/>
      <text x="26" y="76" text-anchor="middle" font-family="Poppins,sans-serif" font-size="13" font-weight="600" fill="#fff">01</text>
      <path d="M120 100c-6-10-22-6-18 6 2 6 18 18 18 18s16-12 18-18c4-12-12-16-18-6z" stroke="#fff" stroke-width="3" fill="none"/>
      <path d="M93 100v22c0 8 10 14 18 18M147 100v22c0 8-10 14-18 18" stroke="#fff" stroke-width="3" fill="none"/>
    </svg>
    <h3>NEQUE PORRO QUISQUAM</h3>
    <p>Lorem Ipsum has been the industry's standard dummy text ever since the 1500s</p>
  </div>
  <div class="divider" style="left:418px"></div>

  <div class="service" style="left:445px">
    <svg width="240" height="200" viewBox="0 0 240 200">
      <path d="M28 146 A100 100 0 0 0 214 148" stroke="#f7941d" stroke-width="3" fill="none"/>
      <path d="M206 138 L226 124 L226 150 Z" fill="none" stroke="#f7941d" stroke-width="3" stroke-linejoin="round"/>
      <circle cx="120" cy="110" r="76" fill="#f7941d"/>
      <circle cx="24" cy="152" r="17" fill="#f7941d"/>
      <text x="24" y="157" text-anchor="middle" font-family="Poppins,sans-serif" font-size="13" font-weight="600" fill="#fff">02</text>
      <path d="M120 140c-30-20-42-32-40-46 2-16 26-20 40-4 14-16 38-12 40 4 2 14-10 26-40 46z" stroke="#fff" stroke-width="3" fill="none"/>
      <path d="M85 112h18l6-12 8 22 6-10h30" stroke="#fff" stroke-width="3" fill="none"/>
    </svg>
    <h3>NEQUE PORRO QUISQUAM</h3>
    <p>Lorem Ipsum has been the industry's standard dummy text ever since the 1500s</p>
  </div>
  <div class="divider" style="left:770px"></div>

  <div class="service" style="left:798px">
    <svg width="240" height="200" viewBox="0 0 240 200">
      <path d="M30 78 A100 100 0 0 1 214 72" stroke="#f7941d" stroke-width="3" fill="none"/>
      <path d="M204 80 L228 70 L222 94 Z" fill="none" stroke="#f7941d" stroke-width="3" stroke-linejoin="round"/>
      <circle cx="120" cy="110" r="76" fill="#f7941d"/>
      <circle cx="26" cy="71" r="17" fill="#f7941d"/>
      <text x="26" y="76" text-anchor="middle" font-family="Poppins,sans-serif" font-size="13" font-weight="600" fill="#fff">03</text>
      <path d="M120 144c-24-14-34-28-32-42 2-14 20-18 32-6 12-12 30-8 32 6 2 14-8 28-32 42z" stroke="#fff" stroke-width="3" fill="none"/>
      <path d="M113 90v-16M125 90v-14" stroke="#fff" stroke-width="3"/>
    </svg>
    <h3>NEQUE PORRO QUISQUAM</h3>
    <p>Lorem Ipsum has been the industry's standard dummy text ever since the 1500s</p>
  </div>

  <a class="btn-orange">GET STARTED NOW</a>
</section>

<section class="abs news">
  <h2>OUR NEWS</h2>

  <article class="abs card-main" role="img" aria-label="Photo of an open AED case with training pads beside a manikin">
    <div class="date">MAR<br>03</div>
    <div class="overlay"></div>
    <h4>Neque porro quisquam est qui dolorem ipsum quia dolor sit amet</h4>
    <div class="meta">
      <svg width="16" height="18" viewBox="0 0 16 18"><path d="M0 0l16 9-16 9z" fill="#fff"/></svg>
      <span class="views" style="margin-left:14px">1239</span>
      <span class="more" style="margin-left:72px">
        <svg width="16" height="20" viewBox="0 0 16 20"><path d="M6 18V4a2 2 0 014 0v7l4 1v6" stroke="#fff" stroke-width="1.5" fill="none"/></svg>
        Read More</span>
    </div>
  </article>

  <article class="abs card-side" style="top:157px">
    <div class="thumb" role="img" aria-label="Photo of hands placing AED pads on a training manikin" style="background:linear-gradient(135deg,#cfd6de,#9ca7b3 50%,#c98f86)"></div>
    <div class="date">FEB<br>18</div>
    <div class="body">
      <h4>Neque porro quisquam est qui dolorem</h4>
      <p>Lorem Ipsum is simply dummy text of the printing and typesetting industry. Lorem Ipsum has been the industry's standard dummy text ever since</p>
    </div>
    <div class="meta">
      <svg style="margin-left:20px" width="16" height="18" viewBox="0 0 16 18"><path d="M0 0l16 9-16 9z" fill="#111"/></svg>
      <span class="views" style="margin-left:18px">1239</span>
      <span class="more"><svg width="16" height="20" viewBox="0 0 16 20"><path d="M6 18V4a2 2 0 014 0v7l4 1v6" stroke="#555" stroke-width="1.5" fill="none"/></svg>Read More</span>
    </div>
  </article>

  <article class="abs card-side" style="top:405px">
    <div class="thumb" role="img" aria-label="Photo of a red AED cabinet sign on a wall" style="background:linear-gradient(90deg,#e6e6e6 0%,#d4d4d4 30%,#c8282c 45%,#b82024 100%)"></div>
    <div class="date">DEC<br>13</div>
    <div class="body">
      <h4>Neque porro quisquam est qui dolorem</h4>
      <p>Lorem Ipsum is simply dummy text of the printing and typesetting industry. Lorem Ipsum has been the industry's standard dummy text ever since</p>
    </div>
    <div class="meta">
      <svg style="margin-left:20px" width="16" height="18" viewBox="0 0 16 18"><path d="M0 0l16 9-16 9z" fill="#111"/></svg>
      <span class="views" style="margin-left:18px">1049</span>
      <span class="more"><svg width="16" height="20" viewBox="0 0 16 20"><path d="M6 18V4a2 2 0 014 0v7l4 1v6" stroke="#555" stroke-width="1.5" fill="none"/></svg>Read More</span>
    </div>
  </article>
</section>

<section>
  <div class="abs map" role="img" aria-label="Light grey street map of New York City and Long Island with location pins marking participating regions"></div>
  <form class="abs form-card">
    <h3>SEND MESSAGE</h3>
    <div class="field" style="left:70px;top:96px;width:328px;height:49px">Enter Your Name</div>
    <div class="field" style="left:419px;top:96px;width:329px;height:49px">Enter Your Email</div>
    <div class="field" style="left:70px;top:169px;width:678px;height:152px">Message</div>
    <div class="btn-submit">SUBMIT</div>
  </form>
</section>

<section>
  <div class="abs info" style="left:133px">
    <div class="icon"><svg width="28" height="24" viewBox="0 0 28 24"><path d="M1 4l8-3 10 3 8-3v19l-8 3-10-3-8 3z M9 1v19 M19 4v19" stroke="#8a9ab8" stroke-width="1.6" fill="none"/></svg></div>
    <div><h5>OFFICE ADDRESS</h5><p>412 Linden Row,<br>Oakhollow, NY 10000</p></div>
  </div>
  <div class="abs info" style="left:452px">
    <div class="icon"><svg width="28" height="22" viewBox="0 0 28 22"><path d="M2 8c0-4 24-4 24 0v3h-6V8H8v3H2z" fill="#555"/><rect x="6" y="11" width="16" height="10" rx="2" fill="#555"/><circle cx="14" cy="16" r="3" fill="#fff"/></svg></div>
    <div><h5>TOLL FREE NUMBER</h5><p>800 555 0142</p></div>
  </div>
  <div class="abs info" style="left:764px">
    <div class="icon"><svg width="26" height="20" viewBox="0 0 26 20"><rect x="1" y="1" width="24" height="18" fill="none" stroke="#555" stroke-width="1.6"/><path d="M1 1l12 10L25 1M1 19l9-9M25 19l-9-9" stroke="#555" stroke-width="1.6" fill="none"/></svg></div>
    <div><h5>SEND MAIL</h5><p>hello@aedlocator.org</p></div>
  </div>
</section>

<footer class="abs footer">
  <div class="ring"></div>
  <div class="sep"></div>
  <div class="name">Birchfield Vale<small>CHAPTER</small></div>
  <nav>
    <a>Home</a><a>About Us</a><a>Services &amp; Products</a><a>Resources</a><a>Blog</a><a>Contact Us</a>
  </nav>
  <div class="social" aria-label="Social links"><span></span><span></span><span></span><span></span></div>
  <p class="copy">© 2019 Copyrights | All Rights Reserved</p>
</footer>

</body>
</html>
```